Business card for marketing analytics company

Need a business card for new company. I have a logo already that I want to be built into the card and should use those colours

Company is called steered by tallies
Design must bring steered by tallies to life not be a card that could be for anyone with a logo put on it.

Like the front to be fairly clean and uncluttered bringing the logo out with a suitable design on the back of the card.

The logo represents a compass and business growth so those themes along with numbers, analytics , data are appropriate.
I'm often working with creative industries so also needs to reflect the creative side of analytics rather than be very corporate looking.

Target Market(s)

Ad agency, media agency, consumer goods clients

Industry/Entity Type

Market Research

Contact Information for Business Card

Needs to include name, title, email and phone number

Colors
f78f20
f68d4d
ec1f27

Requirements
Must have
• Must bring steered by tallies to life not be a card that could be for anyone with a logo put on it.
• Logo, Correct colours
• Like a design on the back that relates to company name
• Designs for both sides
Should not have
• Please do not just submit logo and a coloured card.
• It needs to have a design element to it
• No black background
• No clear cards - needs front & back

```html
<!DOCTYPE html>
<html lang="en">
<head>
<meta charset="utf-8">
<title>Steered by Tallies – Business Card</title>
<link href="https://fonts.googleapis.com/css2?family=Source+Sans+3:wght@400;600&display=swap" rel="stylesheet">
<style>
  :root {
    --backdrop: #2a2a2a;
    --card-white: #ffffff;
    --brand-orange: #f37324;
    --brand-red: #c8102e;
    --text-slate: #4b5056;
    --faint-ring: #f6dedd;
    --back-tint: rgba(255, 255, 255, 0.14);
    --back-tint-strong: rgba(255, 255, 255, 0.22);
  }
  * { margin: 0; padding: 0; box-sizing: border-box; }
  html, body {
    width: 1200px;
    height: 987px;
    overflow: hidden;
    background: var(--backdrop);
    font-family: "Source Sans 3", sans-serif;
  }
  .canvas { position: relative; width: 1200px; height: 987px; }

  .card {
    position: absolute;
    left: 293px;
    width: 615px;
    height: 352px;
    overflow: hidden;
  }
  .card--front { top: 130px; background: var(--card-white); }
  .card--back { top: 505px; background: var(--brand-orange); }

  /* Front */
  .brand-band {
    position: absolute;
    left: 0; top: 43px;
    width: 94px; height: 104px;
    background: var(--brand-orange);
  }
  .brand-dot {
    position: absolute;
    left: 48px; top: 47px;
    width: 98px; height: 98px;
    border-radius: 50%;
    background: var(--card-white);
    border: 3px solid var(--brand-orange);
  }
  .faint-ring {
    position: absolute;
    left: 357px; top: 45px;
    width: 258px; height: 258px;
    border-radius: 50%;
    border: 5px solid var(--faint-ring);
  }
  .wordmark {
    position: absolute;
    font-weight: 600;
    line-height: 1.05;
    white-space: nowrap;
  }
  .card--front .wordmark {
    left: 164px; top: 60px;
    font-size: 29px;
    color: var(--brand-orange);
  }
  .holder { position: absolute; left: 164px; top: 176px; }
  .holder__name {
    font-size: 21px;
    font-weight: 600;
    color: var(--brand-orange);
    letter-spacing: 0.01em;
  }
  .holder__title {
    font-size: 16px;
    color: var(--brand-red);
    margin-top: -2px;
  }
  .contacts {
    position: absolute;
    left: 164px; top: 238px;
    list-style: none;
    font-size: 15px;
    color: var(--text-slate);
  }
  .contacts li {
    display: flex;
    align-items: center;
    gap: 7px;
    height: 23.5px;
  }
  .contacts svg { width: 13px; height: 13px; fill: var(--brand-orange); flex: none; }

  /* Back */
  .back-ring {
    position: absolute;
    left: 430px; top: -70px;
    width: 250px; height: 250px;
    border-radius: 50%;
    border: 5px solid var(--back-tint);
  }
  .back-chart {
    position: absolute;
    left: 28px; bottom: 0;
    width: 120px; height: 96px;
  }
  .back-chart rect { fill: var(--back-tint); }
  .back-chart rect.is-peak { fill: var(--back-tint-strong); }
  .back-dot {
    position: absolute;
    left: 140px; top: 122px;
    width: 106px; height: 106px;
    border-radius: 50%;
    border: 3px solid var(--card-white);
  }
  .card--back .wordmark {
    left: 271px; top: 142px;
    font-size: 32px;
    color: var(--card-white);
  }
  .back-rule {
    position: absolute;
    left: 257px; top: 272px;
    width: 100px; height: 1px;
    background: var(--back-tint-strong);
  }
  .back-url {
    position: absolute;
    left: 0; right: 0; top: 290px;
    text-align: center;
    font-size: 15px;
    letter-spacing: 0.45em;
    color: var(--card-white);
  }
</style>
</head>
<body>
<div class="canvas">

  <section class="card card--front" aria-label="Card front">
    <div class="faint-ring"></div>
    <div class="brand-band"></div>
    <div class="brand-dot"></div>
    <div class="wordmark">Steered by<br>&nbsp;&nbsp;&nbsp;&nbsp;&nbsp;Tallies</div>

    <div class="holder">
      <p class="holder__name">MARA ELLISON</p>
      <p class="holder__title">CEO/Founder</p>
    </div>

    <ul class="contacts">
      <li>
        <svg viewBox="0 0 24 24" aria-hidden="true"><path d="M6.6 10.8a15.1 15.1 0 0 0 6.6 6.6l2.2-2.2c.3-.3.7-.4 1-.2 1.1.4 2.3.6 3.6.6.6 0 1 .4 1 1V20c0 .6-.4 1-1 1A17 17 0 0 1 3 4c0-.6.4-1 1-1h3.5c.6 0 1 .4 1 1 0 1.3.2 2.5.6 3.6.1.3 0 .7-.2 1z"/></svg>
        555 014 2290
      </li>
      <li>
        <svg viewBox="0 0 24 24" aria-hidden="true"><path d="M2 5h20v14H2z"/><path d="M3 6l9 7 9-7" fill="none" stroke="#fff" stroke-width="1.6"/></svg>
        mara@steeredbytallies.com
      </li>
      <li>
        <svg viewBox="0 0 24 24" aria-hidden="true"><circle cx="12" cy="12" r="10"/><path d="M2 12h20M12 2c3 3 3 17 0 20M12 2c-3 3-3 17 0 20" fill="none" stroke="#fff" stroke-width="1.4"/></svg>
        www.steeredbytallies.com
      </li>
    </ul>
  </section>

  <section class="card card--back" aria-label="Card back">
    <div class="back-ring"></div>
    <svg class="back-chart" viewBox="0 0 120 96" aria-hidden="true">
      <rect x="0" y="64" width="16" height="32"/>
      <rect x="26" y="44" width="16" height="52"/>
      <rect x="52" y="54" width="16" height="42"/>
      <rect x="78" y="26" width="16" height="70"/>
      <rect class="is-peak" x="104" y="6" width="16" height="90"/>
    </svg>
    <div class="back-dot"></div>
    <div class="wordmark">Steered by<br>&nbsp;&nbsp;&nbsp;Tallies</div>
    <div class="back-rule"></div>
    <p class="back-url">www.steeredbytallies.com</p>
  </section>

</div>
</body>
</html>
```